Company brochure for our unique consulting business

We are a small consulting business offering a unique set of services to our clients.. In simple terms we are a business improvement consultancy helping our clients get the best out of their businesses. We work with clients across multiple sectors and deliver a variety of services. We want to put together a brochure to cover these main themes:1. Who we are2. What we do3. The type of people we employ4. The sectors we work inWhile the brochure needs to have a certain corporate feel to it, we don't want it to be "boring" or "stiff". We would like it to have a slightly "friendly" or "informal" feel to it, to reflect the type of organisation we are.We have a company website http://brevalconsultingpartners.net , however we do not want to directly replicate the content or feel as we recognise it needs updating.We would like the brochure to be A4 portrait format. We anticipate requiring 12 sides (including covers) but we are happy to be guided on this based on the content we have provided.The attached ppt file gives the detail of the content to be included and also shows the proposed pagination. For the front cover we would like to try 2 versions, one with the BCP logo and one with the Breval Consulting Partners logo (a file of both is attached)One of the most important pages will be the "Our Services" page. We would like this to cover the centre fold. In the ppt file we have shown an example layout, but this is where we need most help - we are clearly not graphic designers! This page will be the most used page in sales meetings etc.Also attached is the following:1. file for our BrevalConsulting Partners company logo.2. File for our BCP company logo3. Files for Derek's signatures (for under photos) - Owen's to follow4. Photo of Derek & Owen (person in purple shirt to be cropped out)Thank you and really excited to see what everyone comes back with.Derek & Owen

Target Market(s)

Very broad - Manufacturing, Healthcare, Hospitality

Industry/Entity Type

Management Consulting

Font styles to use
Other font styles liked:
• We use Swiss721, but happy to be guided by designer

Colors
3276b5
85abd2
0355a3
333333
5c5c5c
9d9d9d
d9d9d9

Requirements
Must have
• Corporate feel
Nice to have
• Slightly friendly feel
• Our standard "blue" is (CORRECTION) - R55 G96 B146 #376092 and our standard grey is R197 G178, B179 - #B3B2B2, which we would like to keep, but other colours we are happy to be guided on. Brand guidelines attached.

```html
<!DOCTYPE html>
<html lang="en">
<head>
<meta charset="utf-8">
<title>Our Values – Breval Consulting Partners</title>
<link rel="stylesheet" href="https://fonts.googleapis.com/css2?family=Arimo:wght@400;700&display=swap">
<style>
  :root {
    --brand-blue: #2750d5;
    --band-blue: #2a4fc9;
    --band-blue-dark: #2244b4;
    --rule-grey: #3c4650;
    --panel-grey: #dcdedd;
    --photo-light: #d8d8d8;
    --photo-mid: #9a9a9a;
    --photo-dark: #5c5c5c;
    --ink: #111111;
    --paper: #ffffff;
  }
  * { margin: 0; padding: 0; box-sizing: border-box; }
  html, body { width: 848px; height: 1200px; overflow: hidden; background: var(--paper); }
  body { font-family: "Arimo", "Helvetica Neue", Arial, sans-serif; color: var(--ink); }

  .page { position: relative; width: 848px; height: 1200px; overflow: hidden; background: var(--paper); }

  .page-shapes { position: absolute; inset: 0; width: 848px; height: 1200px; }

  .brand-name {
    position: absolute; left: 70px; top: 36px;
    font-size: 38px; font-weight: 700; letter-spacing: 1px;
    color: #2b2f36;
  }

  .page-title {
    position: absolute; left: 390px; top: 72px;
    font-size: 34px; font-weight: 700; color: var(--paper);
  }

  .values-list { position: absolute; left: 196px; top: 414px; width: 572px; list-style: none; }
  .value-item { position: relative; padding-left: 40px; font-size: 16px; line-height: 30px; text-align: justify; }
  .value-item::before {
    content: ""; position: absolute; left: 0; top: 0;
    border-left: 26px solid var(--ink);
    border-top: 14px solid transparent; border-bottom: 14px solid transparent;
  }
  .value-item + .value-item { margin-top: 27px; }
  .value-item.spaced { margin-top: 33px; }

  .footer-band {
    position: absolute; left: 0; top: 1124px; width: 848px; height: 76px;
    background: linear-gradient(180deg, var(--band-blue) 0%, var(--band-blue-dark) 100%);
  }
  .page-number {
    position: absolute; left: 50px; top: 1148px;
    font-size: 20px; color: var(--paper);
  }
</style>
</head>
<body>
<main class="page">
  <svg class="page-shapes" viewBox="0 0 848 1200" aria-hidden="false">
    <defs>
      <linearGradient id="cityTones" x1="0" y1="0" x2="1" y2="1">
        <stop offset="0" stop-color="var(--photo-mid)"/>
        <stop offset="0.45" stop-color="var(--photo-light)"/>
        <stop offset="1" stop-color="var(--photo-dark)"/>
      </linearGradient>
    </defs>
    <polygon class="logo-panel" points="0,0 256,0 344,96 0,96" fill="var(--panel-grey)"/>
    <polygon class="header-rule" points="360,124 848,124 848,131 366,131" fill="var(--rule-grey)"/>
    <polygon class="header-band" points="256,0 848,0 848,124 360,124" fill="var(--brand-blue)"/>
    <polygon class="city-photo" points="0,96 344,96 364,128 0,632" fill="url(#cityTones)"
             role="img" aria-label="Black and white photo looking up at glass office towers against a cloudy sky"/>
  </svg>

  <div class="brand-name">BCP</div>
  <h1 class="page-title">Our Values</h1>

  <ul class="values-list">
    <li class="value-item">Be TRUSTED by our team and clients, so that our opinions are sought and our recommendations valued.</li>
    <li class="value-item">Have a tight knit relationship with our clients, so we are seen as a PARTNER and not just supplier.</li>
    <li class="value-item">Be focused on return-on-investment, but predominantly, always deliver GREAT VALUE.</li>
    <li class="value-item spaced">DEVELOP &amp; INVEST IN our own people to continually stay one step ahead.</li>
    <li class="value-item spaced">Work relentlessly to deliver results for our clients, but ensure we collectively ENJOY THE JOURNEY.</li>
    <li class="value-item spaced">Take SOCIAL RESPONSIBILITY seriously by supporting other worthwhile organisations.</li>
  </ul>

  <div class="footer-band"></div>
  <div class="page-number">3</div>
</main>
</body>
</html>
```